Structural Engineering Business Card

Brookvane Drafting does residential house plans for clients in Central Florida. Would like simple but elegant business card that is appropriate for a house plan engineering company. Prefer black business card with black/white them but open to other shades of blue. I uploaded a sample card that I came across that looked good but please come up with your own creative designs.

Contact Information for Business Card

Name, Title, Phone, Email, Address, website

```html
<!DOCTYPE html>
<html lang="en">
<head>
<meta charset="utf-8">
<title>Brookvane Drafting – Business Card</title>
<link href="https://fonts.googleapis.com/css2?family=Montserrat:wght@400;500;800&display=swap" rel="stylesheet">
<style>
  :root {
    --page-bg: #d9d6d1;
    --card-bg: #eceeef;
    --card-edge: #f7f8f8;
    --ink: #161616;
    --ink-soft: #2b2b2b;
    --map-fill: #0f0f0f;
  }
  html, body {
    margin: 0;
    padding: 0;
    width: 1200px;
    height: 887px;
    overflow: hidden;
    background: var(--page-bg);
    font-family: "Montserrat", sans-serif;
  }
  .card {
    position: absolute;
    left: 80px;
    top: 160px;
    width: 1040px;
    height: 568px;
    background: var(--card-bg);
    border: 2px solid var(--card-edge);
    border-radius: 26px;
    overflow: hidden;
    box-sizing: border-box;
  }
  .state-map {
    position: absolute;
    left: 0;
    top: 0;
    width: 740px;
    height: 568px;
  }
  .contact {
    position: absolute;
    left: 62px;
    top: 268px;
    color: var(--ink);
  }
  .contact-name {
    margin: 0;
    font-size: 30px;
    font-weight: 500;
    letter-spacing: 0.5px;
    text-transform: uppercase;
  }
  .contact-title {
    margin: 2px 0 0;
    font-size: 21px;
    font-weight: 400;
    letter-spacing: 0.6px;
    text-transform: uppercase;
    color: var(--ink-soft);
  }
  .contact-address {
    margin: 22px 0 0;
    font-size: 22px;
    line-height: 32px;
    font-style: normal;
    color: var(--ink-soft);
  }
  .contact-lines {
    list-style: none;
    margin: 18px 0 0;
    padding: 0;
    font-size: 21px;
    line-height: 32px;
    color: var(--ink-soft);
  }
  .contact-lines li {
    display: flex;
    align-items: center;
    gap: 6px;
  }
  .contact-lines svg {
    width: 16px;
    height: 16px;
    flex: none;
  }
  .brand-name {
    position: absolute;
    left: 868px;
    top: 50%;
    transform: translateY(-50%) rotate(180deg);
    writing-mode: vertical-rl;
    margin: 0;
    font-size: 34px;
    line-height: 1;
    font-weight: 800;
    letter-spacing: 0.5px;
    text-transform: uppercase;
    color: var(--ink);
    white-space: nowrap;
  }
</style>
</head>
<body>
  <section class="card">
    <svg class="state-map" viewBox="0 0 740 568" role="img" aria-label="Large black silhouette map of the state of Florida">
      <path d="M0 0 H740 V568 H455 V150 H0 Z" fill="var(--map-fill)"/>
    </svg>

    <div class="contact">
      <h1 class="contact-name">Daniel Harper</h1>
      <p class="contact-title">Director</p>
      <address class="contact-address">1458 Orchard Lane<br>Orlando, FL 32801</address>
      <ul class="contact-lines">
        <li>
          <svg viewBox="0 0 16 16" aria-hidden="true"><path d="M4 1.5 L6.5 4.5 L5 6.2 C6 8.3 7.7 10 9.8 11 L11.5 9.5 L14.5 12 L13 14.5 C7 14 2 9 1.5 3 Z" fill="none" stroke="currentColor" stroke-width="1.4" stroke-linejoin="round"/></svg>
          407.555.0192
        </li>
        <li>
          <svg viewBox="0 0 16 16" aria-hidden="true"><rect x="1.5" y="3.5" width="13" height="9" fill="none" stroke="currentColor" stroke-width="1.4"/><path d="M1.5 3.5 L8 9 L14.5 3.5" fill="none" stroke="currentColor" stroke-width="1.4"/></svg>
          info@BrookvaneDrafting.com
        </li>
        <li>
          <svg viewBox="0 0 16 16" aria-hidden="true"><circle cx="8" cy="8" r="6.5" fill="none" stroke="currentColor" stroke-width="1.3"/><ellipse cx="8" cy="8" rx="2.8" ry="6.5" fill="none" stroke="currentColor" stroke-width="1.1"/><path d="M1.5 8 H14.5 M2.6 4.8 H13.4 M2.6 11.2 H13.4" stroke="currentColor" stroke-width="1.1"/></svg>
          www.BrookvaneDrafting.com
        </li>
      </ul>
    </div>

    <p class="brand-name">Brookvane Drafting</p>
  </section>
</body>
</html>
```